Stylish Business Cards Wanted

- DOUBLE SIDED Design Required -

High end, edgy cards for a corporate and personal stylist. Must include logo,
Name: Belinda Harwick
Title: Director and Stylist
telephone : +61 8 7142 5809
email: belinda@theloombriefing.example
website: theloombriefing.example
Tag: Corporate Workwear & Uniform Specialist | Personal Stylist
Would like nice icons for telephone, email, website

Target Market(s)

Businesses wanting stylish uniforms, people wanting stylish wardrobes

Industry/Entity Type

Corporate Workwear Stylist

Contact Information for Business Card

I would like black, white and gold foiling incorporated in the design - possibly a touch of the other colours on my branding guide attached Name: Belinda Harwick Title: Director and Stylist telephone : +61 8 7142 5809 email: belinda@theloombriefing.example website: theloombriefing.example Tag: Corporate Workwear & Uniform Specialist | Personal Stylist Would like nice icons for telephone, email, website

Font styles to use
Other font styles liked:
• Raleway

Colors

Designer to choose colors to be used in the design.

Requirements
Must have
• Gold foil accents

```html
<!DOCTYPE html>
<html lang="en">
<head>
<meta charset="utf-8">
<title>The Loom Briefing – Business Cards</title>
<link href="https://fonts.googleapis.com/css2?family=Montserrat:wght@400;500;600&family=Raleway:wght@400;500&family=Yellowtail&display=swap" rel="stylesheet">
<style>
  :root {
    --page-bg: #d6d6d6;
    --card-black: #231f20;
    --gold: #c9a13f;
    --gold-edge: #d8b44a;
    --white: #f4f4f4;
    --grey-text: #cfcfcf;
  }
  * { box-sizing: border-box; margin: 0; padding: 0; }
  html, body {
    width: 1200px; height: 800px; overflow: hidden;
    background: var(--page-bg);
  }
  .sheet {
    width: 1200px; height: 800px;
    display: flex; align-items: center; justify-content: center; gap: 48px;
  }
  .card {
    position: relative;
    width: 525px; height: 300px;
    background: var(--card-black);
    border-right: 3px solid var(--gold-edge);
    border-bottom: 3px solid var(--gold-edge);
    box-shadow: 0 14px 30px rgba(0,0,0,0.25);
    color: var(--white);
  }

  /* Contact side */
  .card--contact {
    display: flex; flex-direction: column; align-items: center; justify-content: center;
  }
  .contact__name {
    font-family: 'Yellowtail', cursive;
    font-size: 46px; line-height: 1;
    color: var(--white);
  }
  .contact__title {
    font-family: 'Raleway', sans-serif;
    font-size: 15px; letter-spacing: 0.5px;
    color: var(--gold);
    margin-top: 6px;
  }
  .contact__rule {
    width: 34px; height: 1px; background: var(--grey-text);
    margin: 12px 0 14px;
  }
  .contact__list { list-style: none; }
  .contact__item {
    display: flex; align-items: center; gap: 8px;
    font-family: 'Raleway', sans-serif;
    font-size: 14px; line-height: 22px;
    color: var(--grey-text);
  }
  .contact__icon { width: 13px; height: 13px; flex: none; }
  .contact__list { display: flex; flex-direction: column; align-items: center; }

  /* Brand side */
  .card--brand {
    display: flex; flex-direction: column; align-items: center;
  }
  .brand__name {
    margin-top: 92px;
    font-family: 'Montserrat', sans-serif;
    font-weight: 600;
    font-size: 34px; letter-spacing: 3px;
    text-transform: uppercase;
    color: var(--white);
  }
  .brand__services {
    position: absolute; left: 0; right: 0; bottom: 34px;
    text-align: center;
    font-family: 'Montserrat', sans-serif;
    font-weight: 500;
    font-size: 12.5px; letter-spacing: 1.4px;
    color: var(--grey-text);
  }
  .brand__divider { color: var(--gold); margin: 0 4px; }
</style>
</head>
<body>
<main class="sheet">

  <section class="card card--contact" aria-label="Business card, contact side">
    <h1 class="contact__name">Belinda Harwick</h1>
    <p class="contact__title">Director &amp; Stylist</p>
    <span class="contact__rule"></span>
    <ul class="contact__list">
      <li class="contact__item">
        <svg class="contact__icon" viewBox="0 0 16 16" fill="none" stroke="var(--gold)" stroke-width="1.4" stroke-linejoin="round">
          <path d="M3 1.5h3l1.3 3.5-2 1.3a9 9 0 0 0 4.4 4.4l1.3-2 3.5 1.3v3a1.5 1.5 0 0 1-1.6 1.5A13 13 0 0 1 1.5 3.1 1.5 1.5 0 0 1 3 1.5z"/>
        </svg>
        +61 8 7142 5809
      </li>
      <li class="contact__item">
        <svg class="contact__icon" viewBox="0 0 16 16" fill="none" stroke="var(--gold)" stroke-width="1.4" stroke-linejoin="round">
          <rect x="1" y="3" width="14" height="10" rx="1"/>
          <path d="M1.5 3.5 8 9l6.5-5.5"/>
        </svg>
        belinda@theloombriefing.example
      </li>
      <li class="contact__item">
        <svg class="contact__icon" viewBox="0 0 16 16" fill="none" stroke="var(--gold)" stroke-width="1.3">
          <circle cx="8" cy="8" r="6.5"/>
          <ellipse cx="8" cy="8" rx="2.8" ry="6.5"/>
          <path d="M1.5 8h13"/>
        </svg>
        theloombriefing.example
      </li>
    </ul>
  </section>

  <section class="card card--brand" aria-label="Business card, brand side">
    <p class="brand__name">The Loom Briefing</p>
    <p class="brand__services">
      CORPORATE WORKWEAR<span class="brand__divider">|</span>UNIFORM SPECIALIST<span class="brand__divider">|</span>PERSONAL STYLIST
    </p>
  </section>

</main>
</body>
</html>
```